Business Card Design

New business card design

Target Market(s)

Residential & Commercial Property Managers

Industry/Entity Type

Plumbing Services

Contact Information for Business Card

Name - Rowan Keddle, title - Director, Phone Number - 0431 286 517, email - rowan@tbk-plumbing.com.au, Company ABN - 73 215 904 386,

Font styles to use
Sans Serif

Colors
0054AA
0677BA
7BADD7
CADEEF
E8F1F8

```html
<!DOCTYPE html>
<html lang="en">
<head>
<meta charset="utf-8">
<title>TBK Plumbing Services – Business Card</title>
<link href="https://fonts.googleapis.com/css2?family=Montserrat:wght@400;500;700&display=swap" rel="stylesheet">
<style>
  :root {
    --page: #e9e6e1;
    --ink: #1f2530;
    --paper: #ffffff;
    --accent: #29a8e0;
    --muted: #7d8087;
  }
  * { margin: 0; padding: 0; box-sizing: border-box; }
  html, body { width: 1200px; height: 931px; overflow: hidden; }
  body {
    background: var(--page);
    font-family: "Montserrat", sans-serif;
    position: relative;
  }
  .card {
    position: absolute;
    left: 220px;
    width: 760px;
    height: 434px;
    border-radius: 22px;
    overflow: hidden;
    box-shadow: 0 6px 18px rgba(0,0,0,.18);
  }
  .card--front { top: 21px; background: var(--ink); }
  .card--back { top: 476px; background: var(--paper); }

  .brand { position: absolute; display: flex; flex-direction: column; align-items: flex-end; }
  .brand__row { display: flex; align-items: center; gap: 14px; }
  .brand__name { font-weight: 500; letter-spacing: 4px; line-height: 1; }
  .brand__dot { border-radius: 50%; background: var(--accent); }
  .brand__tag { color: var(--muted); letter-spacing: 9px; font-weight: 400; }

  .card--front .brand { left: 0; right: 0; top: 150px; align-items: center; }
  .card--front .brand__name { color: var(--paper); font-size: 96px; }
  .card--front .brand__dot { width: 26px; height: 26px; }
  .card--front .brand__tag { font-size: 17px; margin-top: 18px; }

  .card--back .brand { right: 50px; top: 44px; }
  .card--back .brand__name { color: var(--ink); font-size: 52px; }
  .card--back .brand__dot { width: 15px; height: 15px; }
  .card--back .brand__tag { font-size: 10px; margin-top: 10px; letter-spacing: 6px; }

  .divider { position: absolute; left: 150px; right: 40px; top: 196px; height: 2px; background: var(--ink); }

  .person { position: absolute; left: 150px; top: 214px; }
  .person__name { font-size: 31px; font-weight: 700; color: var(--ink); line-height: 1.1; }
  .person__role { font-size: 19px; color: var(--ink); margin-top: 2px; }

  .contacts { position: absolute; left: 150px; top: 292px; list-style: none; }
  .contacts li { display: flex; align-items: center; gap: 12px; font-size: 17px; color: var(--ink); height: 27px; }
  .contacts svg { width: 18px; height: 18px; fill: var(--accent); flex: none; }
  .contacts .abn-label { color: var(--accent); font-weight: 700; }

  .address { position: absolute; right: 40px; top: 236px; text-align: right; font-size: 15px; color: var(--ink); line-height: 1.35; }

  .band { position: absolute; left: 0; right: 0; bottom: 0; height: 30px; background: var(--ink); }
  .band__accent { position: absolute; right: 0; bottom: 0; width: 210px; height: 62px; background: var(--accent); border-left: 6px solid var(--paper); }
</style>
</head>
<body>
  <section class="card card--front" aria-label="Card front">
    <div class="brand">
      <div class="brand__row">
        <span class="brand__name">tbk</span>
        <span class="brand__dot"></span>
      </div>
      <span class="brand__tag">plumbing services</span>
    </div>
  </section>

  <section class="card card--back" aria-label="Card back">
    <div class="brand">
      <div class="brand__row">
        <span class="brand__name">tbk</span>
        <span class="brand__dot"></span>
      </div>
      <span class="brand__tag">plumbing services</span>
    </div>

    <div class="divider"></div>

    <div class="person">
      <p class="person__name">Rowan Keddle</p>
      <p class="person__role">Director</p>
    </div>

    <ul class="contacts">
      <li>
        <svg viewBox="0 0 24 24" aria-hidden="true"><path d="M6.6 10.8a15.1 15.1 0 0 0 6.6 6.6l2.2-2.2a1 1 0 0 1 1-.25 11.4 11.4 0 0 0 3.6.57 1 1 0 0 1 1 1V20a1 1 0 0 1-1 1A17 17 0 0 1 3 4a1 1 0 0 1 1-1h3.5a1 1 0 0 1 1 1c0 1.25.2 2.45.57 3.57a1 1 0 0 1-.25 1z"/></svg>
        <span>0431 286 517</span>
      </li>
      <li>
        <svg viewBox="0 0 24 24" aria-hidden="true"><path d="M2 5h20v14H2z M2 5l10 8 10-8" /></svg>
        <span>rowan@tbk-plumbing.com.au</span>
      </li>
      <li>
        <svg viewBox="0 0 24 24" aria-hidden="true"><circle cx="12" cy="12" r="10"/></svg>
        <span>www.tbk-plumbing.com.au</span>
      </li>
      <li>
        <span><span class="abn-label">ABN</span> - 73 215 904 386</span>
      </li>
    </ul>

    <p class="address">48 Harbour Street<br>Wollongong NSW 2500</p>

    <div class="band"></div>
    <div class="band__accent"></div>
  </section>
</body>
</html>
```